K7 Electrical Services Ltd Web design

I require a web site for my new electrical contracting company. We are customer service orientated. Offering high value electrical installations, design and maintenance. Focused on custom residential and commercial upgrading. Lighting design and application are paramount in our company's services. Industry leading product use and integration are always on the forefront with our customer client services. As well as energy efficiency.

Target Market(s)

Homebuilders, General Contractors, Property management companies, clients, individuals,

Industry/Entity Type

Electric Company

Coding

Coded - Design and coding required

Number of Pages Required

3 page

Requirements
Must have
• Classic, modern, edgy but not trendy . Appeals to the masse.
• 3 page
• home page
• about page
• gallery page
• ability to contact from the webiste
Nice to have
• open to all types of designs that are relative to the construction industry.
• Black, Grey, metallic ice blue and deep purple colours from the logo.
Should not have
• anything cheesy with cartoon light bulb images.

```html
<!DOCTYPE html>
<html lang="en">
<head>
<meta charset="utf-8">
<title>K7 Electrical Services Ltd</title>
<link rel="stylesheet" href="https://fonts.googleapis.com/css2?family=Montserrat:wght@400;600;700&family=Open+Sans:wght@400;600&display=swap">
<style>
:root{
  --purple:#5b2c8f;
  --purple-dark:#3f1c6e;
  --purple-light:#7b4bb0;
  --orange:#f7941d;
  --ink:#333333;
  --grey-text:#666666;
  --grey-band:#5f5f61;
  --light:#ebebeb;
  --footer:#f1f1f1;
  --bar:#d8d8d8;
  --white:#ffffff;
}
*{box-sizing:border-box;margin:0;padding:0}
html,body{width:1200px;height:3087px;overflow:hidden}
body{font-family:"Open Sans",Arial,sans-serif;color:var(--ink);background:var(--white);position:relative}
.photo{position:absolute}
.heading{font-family:"Montserrat",Arial,sans-serif;font-weight:700;text-align:center;letter-spacing:1px}
.divider{display:flex;align-items:center;justify-content:center;gap:10px}
.divider span{display:block;width:88px;height:2px;background:var(--purple)}
.divider i{display:block;width:10px;height:10px;border:2px solid var(--purple)}
.divider.light span{background:#fff}.divider.light i{border-color:#fff}
.btn-outline{display:flex;align-items:center;justify-content:center;font-family:"Montserrat",Arial,sans-serif;font-weight:600;font-size:16px;letter-spacing:1px}

/* brand */
.brand{position:absolute;display:flex;align-items:center;gap:12px;font-family:"Montserrat",Arial,sans-serif;font-weight:700;font-size:26px;line-height:31px;letter-spacing:1px;white-space:nowrap}
.brand i{display:block;flex:none;width:20px;height:20px}

/* hero */
.hero{position:absolute;left:0;top:0;width:1200px;height:677px;overflow:hidden}
.hero .photo{inset:0;background:linear-gradient(100deg,#3c4a63 0%,#5d6678 40%,#9a9ea6 70%,#c9cacc 100%)}
.hero .shade{position:absolute;inset:0;background:rgba(20,24,34,.35)}
.hero .brand{left:125px;top:26px;color:#fff}
.hero .brand i{background:#fff}
.phone{position:absolute;right:122px;top:24px;color:#fff;font-size:19px;display:flex;align-items:center;gap:8px}
.nav{position:absolute;left:448px;top:64px;display:flex;font-family:"Montserrat",Arial,sans-serif;font-weight:600;font-size:15px;color:#fff}
.nav a{color:#fff;text-decoration:none;padding:9px 16px;letter-spacing:.5px}
.nav a.active{background:var(--purple);padding:9px 24px}
.hero h1{position:absolute;left:0;width:1200px;top:278px;color:#fff;font-size:38px;line-height:46px;letter-spacing:2px}
.hero h1 small{display:block;font-size:32px;line-height:40px}
.btn-contact{position:absolute;left:515px;top:375px;width:190px;height:48px;background:var(--orange);color:#fff;border-radius:3px}
.dots{position:absolute;left:556px;top:635px;display:flex;gap:10px}
.dots i{width:14px;height:14px;border-radius:50%;background:#fff;display:block}
.dots i.off{background:transparent;border:2px solid #fff}

/* about */
.about{position:absolute;top:677px;left:0;width:1200px;height:388px}
.about h2{position:absolute;top:58px;width:1200px;font-size:30px;color:#555}
.about h2 b{color:var(--purple)}
.about .divider{position:absolute;top:105px;width:1200px}
.about p{position:absolute;left:195px;top:135px;width:810px;text-align:center;font-size:14.5px;line-height:26px;color:#555}
.about .btn-outline{position:absolute;left:515px;top:276px;width:170px;height:44px;border:2px solid var(--purple);color:#444}

/* why */
.why{position:absolute;top:1065px;left:0;width:1200px;height:408px;background:var(--grey-band)}
.why .photo{left:420px;top:0;width:780px;height:408px;background:linear-gradient(110deg,#24314a 0%,#4b5670 35%,#8f949c 70%,#c7c3b6 100%)}
.why h3{position:absolute;left:130px;top:87px;font-family:"Montserrat",Arial,sans-serif;font-size:24px;font-weight:400;color:#fff;letter-spacing:1px}
.why p{position:absolute;left:130px;top:127px;width:395px;font-size:13.5px;line-height:26px;color:#f0f0f0}
.why .btn-outline{position:absolute;left:135px;top:282px;width:132px;height:36px;border:2px solid #fff;color:#fff;font-weight:400;font-size:14px}

/* services */
.services{position:absolute;top:1473px;left:0;width:1200px;height:397px;background:linear-gradient(120deg,var(--purple-light) 0%,var(--purple) 50%,var(--purple-dark) 100%)}
.services h2{position:absolute;top:42px;width:1200px;color:#fff;font-size:28px}
.services .divider{position:absolute;top:88px;width:1200px}
.service{position:absolute;top:140px;width:230px;text-align:center;color:#fff;font-size:16px;line-height:22px;letter-spacing:.5px}
.service svg{display:block;margin:0 auto 18px}

/* projects */
.projects{position:absolute;top:1870px;left:0;width:1200px;height:515px;background:var(--light)}
.projects h2{position:absolute;top:42px;width:1200px;color:var(--purple);font-size:29px}
.projects .divider{position:absolute;top:88px;width:1200px}
.card{position:absolute;top:118px;width:310px;height:329px;background:#fff;box-shadow:0 1px 4px rgba(0,0,0,.15);text-align:center}
.card .photo{position:relative;width:310px;height:189px}
.card h4{font-weight:400;font-size:19px;color:#444;margin-top:20px}
.card p{font-size:12.5px;line-height:19px;color:#555;margin:10px auto 0;width:230px}
.card span{display:block;font-size:12px;font-weight:600;margin-top:6px;color:#222}

/* contact band */
.contact{position:absolute;top:2385px;left:0;width:1200px;height:352px;overflow:hidden}
.contact .photo{inset:0;background:linear-gradient(100deg,#4a4f58 0%,#3a4150 45%,#2b3b55 75%,#3d4c66 100%)}
.contact .shade{position:absolute;inset:0;background:rgba(15,18,26,.45)}
.contact h2{position:absolute;top:86px;width:1200px;color:#fff;font-size:28px}
.contact .divider{position:absolute;top:131px;width:1200px}
.contact p{position:absolute;left:250px;top:150px;width:700px;text-align:center;color:#fff;font-size:18px;line-height:28px}
.contact .btn-outline{position:absolute;left:530px;top:230px;width:150px;height:42px;border:2px solid #fff;color:#fff;font-weight:400;font-size:15px}

/* footer */
.footer{position:absolute;top:2737px;left:0;width:1200px;height:283px;background:var(--footer)}
.footer .brand{left:120px;top:96px;color:var(--purple)}
.footer .brand i{background:var(--purple)}
.fcol{position:absolute;top:70px}
.fcol h5{font-family:"Montserrat",Arial,sans-serif;font-weight:700;font-size:15px;letter-spacing:1px;color:#222;margin-bottom:12px}
.fcol li{list-style:none;font-size:13.5px;line-height:30px;color:#555}
.fcol .row{display:flex;align-items:center;gap:8px}
.socials{display:flex;gap:10px;margin-top:10px}
.socials i{display:block;width:32px;height:32px;border-radius:50%;border:2px solid var(--purple)}
.bar{position:absolute;top:3020px;left:0;width:1200px;height:67px;background:var(--bar);text-align:center;line-height:67px;font-size:13.5px;color:#555}
</style>
</head>
<body>

<header class="hero">
  <div class="photo" role="img" aria-label="Electrician in a hard hat stripping wires at a wall panel"></div>
  <div class="shade"></div>
  <div class="brand"><i></i><span>K7 Electrical<br>Services</span></div>
  <div class="phone">
    <svg width="18" height="18" viewBox="0 0 24 24"><path fill="#fff" d="M6.6 10.8a15 15 0 0 0 6.6 6.6l2.2-2.2c.3-.3.7-.4 1-.2 1.1.4 2.3.6 3.6.6.6 0 1 .4 1 1V20c0 .6-.4 1-1 1A17 17 0 0 1 3 4c0-.6.4-1 1-1h3.5c.6 0 1 .4 1 1 0 1.3.2 2.5.6 3.6.1.3 0 .7-.2 1z"/></svg>
    (555) 014 2290
  </div>
  <nav class="nav">
    <a class="active">HOME</a><a>ABOUT US</a><a>SERVICES</a><a>PROJECTS</a><a>WHY US</a><a>CONTACT</a>
  </nav>
  <h1 class="heading">ELECTRICAL CONTRACTING AND<small>DESIGN AND MAINTENANCE</small></h1>
  <div class="btn-outline btn-contact">CONTACT US</div>
  <div class="dots"><i class="off"></i><i></i><i></i><i></i></div>
</header>

<section class="about">
  <h2 class="heading">ABOUT <b>K7 ELECTRICAL</b></h2>
  <div class="divider"><span></span><i></i><span></span></div>
  <p>Vivamus porttitor purus nisi eleifend libero a tempus libero lectus feugiat felis Morbi diam mauris viverra in gravida eu mattis in ante Morbi eget arcu Morbi porta libero id ullamcorper nonummy nibh ligula pulvinar metus eget consectetuer augue nisi quis lacus Ut ac mi quis lacus mollis aliquam Curabitur iaculis tempus eros Curabitur vel mi sit amet magna malesuada ultrices Ut nisi erat fermentum vel congue id euismod in elit</p>
  <div class="btn-outline">READ MORE</div>
</section>

<section class="why">
  <div class="photo" role="img" aria-label="Electrician checking wiring in an open distribution cabinet"></div>
  <h3>WHY WE ARE</h3>
  <p>Vivamus porttitor purus nisi eleifend libero a tempus libero lectus feugiat felis Morbi diam mauris viverra in gravida eu mattis in ante Morbi eget arcu Morbi porta libero id ullamcorper nonummy nibh ligula pulvinar metus eget consectetuer augue nisi quis lacus Ut ac mi</p>
  <div class="btn-outline">READ MORE</div>
</section>

<section class="services">
  <h2 class="heading">SERVICES PROVIDE</h2>
  <div class="divider light"><span></span><i></i><span></span></div>
  <div class="service" style="left:107px">
    <svg width="96" height="96" viewBox="0 0 96 96"><polygon points="48,4 86,26 86,70 48,92 10,70 10,26" fill="none" stroke="rgba(255,255,255,.7)" stroke-width="2"/><path d="M36 58h24M40 58v-8h16v8M44 50V40M52 50V40M48 58v8" stroke="#fff" stroke-width="3" fill="none"/></svg>
    ELECTRICAL<br>INSTALLATIONS
  </div>
  <div class="service" style="left:356px">
    <svg width="96" height="96" viewBox="0 0 96 96"><polygon points="48,4 86,26 86,70 48,92 10,70 10,26" fill="none" stroke="rgba(255,255,255,.7)" stroke-width="2"/><rect x="34" y="34" width="24" height="28" rx="3" fill="none" stroke="#fff" stroke-width="3"/><rect x="40" y="28" width="24" height="28" rx="3" fill="none" stroke="#fff" stroke-width="3"/><circle cx="46" cy="48" r="5" fill="none" stroke="#fff" stroke-width="2.5"/></svg>
    DESIGN AND<br>MAINTENANCE
  </div>
  <div class="service" style="left:605px">
    <svg width="96" height="96" viewBox="0 0 96 96"><polygon points="48,4 86,26 86,70 48,92 10,70 10,26" fill="none" stroke="rgba(255,255,255,.7)" stroke-width="2"/><rect x="36" y="28" width="24" height="38" rx="3" fill="none" stroke="#fff" stroke-width="3"/><rect x="40" y="33" width="16" height="9" fill="#fff"/><circle cx="48" cy="54" r="5" fill="none" stroke="#fff" stroke-width="2.5"/></svg>
    RESIDENTIAL AND<br>COMMERCIAL UPGRADING
  </div>
  <div class="service" style="left:854px">
    <svg width="96" height="96" viewBox="0 0 96 96"><polygon points="48,4 86,26 86,70 48,92 10,70 10,26" fill="none" stroke="rgba(255,255,255,.7)" stroke-width="2"/><rect x="34" y="28" width="28" height="38" rx="3" fill="none" stroke="#fff" stroke-width="3"/><circle cx="48" cy="44" r="7" fill="none" stroke="#fff" stroke-width="2.5"/><path d="M45 52h6M45 56h6" stroke="#fff" stroke-width="2.5"/></svg>
    LIGHTING DESIGN AND<br>APPLICATION
  </div>
</section>

<section class="projects">
  <h2 class="heading">OUR PROJECTS</h2>
  <div class="divider"><span></span><i></i><span></span></div>
  <article class="card" style="left:117px">
    <div class="photo" style="background:linear-gradient(135deg,#dfe3e8,#a9b0b8)" role="img" aria-label="Row of circuit breakers in a distribution board"></div>
    <h4>Project Title here</h4>
    <p>Ut nisi erat fermentum vel congue id euismod in elit Fusce ultricies orci</p>
    <span>READ MORE</span>
  </article>
  <article class="card" style="left:442px">
    <div class="photo" style="background:linear-gradient(135deg,#5c6470,#b9bdc3)" role="img" aria-label="Technician fitting a ceiling light panel"></div>
    <h4>Project Title here</h4>
    <p>Ut nisi erat fermentum vel congue id euismod in elit Fusce ultricies orci</p>
    <span>READ MORE</span>
  </article>
  <article class="card" style="left:768px">
    <div class="photo" style="background:linear-gradient(135deg,#2c3848,#8a5a2c 60%,#d9913a)" role="img" aria-label="Warm pendant lamps hanging in a room"></div>
    <h4>Project Title here</h4>
    <p>Ut nisi erat fermentum vel congue id euismod in elit Fusce ultricies orci</p>
    <span>READ MORE</span>
  </article>
</section>

<section class="contact">
  <div class="photo" role="img" aria-label="Electrician working on an industrial switchboard"></div>
  <div class="shade"></div>
  <h2 class="heading">CONTACT US NOW</h2>
  <div class="divider light"><span></span><i></i><span></span></div>
  <p>Ut nisi erat fermentum vel congue id euismod in elit Fusce ultricies orci ac feugiat suscipit leo massa sodales velit et scelerisque mi tortor</p>
  <div class="btn-outline">CLICK HERE</div>
</section>

<footer class="footer">
  <div class="brand"><i></i><span>K7 Electrical<br>Services</span></div>
  <div class="fcol" style="left:408px">
    <h5>QUICK LINKS</h5>
    <ul><li>About Us</li><li>Why Us</li><li>Services</li><li>Contact Us</li></ul>
  </div>
  <div class="fcol" style="left:588px">
    <h5>SERVICES</h5>
    <ul><li>Electrical installations</li><li>Design and maintenance</li><li>Commercial upgrading</li><li>Lighting design</li></ul>
  </div>
  <div class="fcol" style="left:814px">
    <h5>CONTACT US</h5>
    <ul>
      <li class="row"><svg width="12" height="14" viewBox="0 0 24 28"><path fill="#5b2c8f" d="M12 0a10 10 0 0 0-10 10c0 7 10 18 10 18s10-11 10-18A10 10 0 0 0 12 0zm0 14a4 4 0 1 1 0-8 4 4 0 0 1 0 8z"/></svg>48 Harlow Street #6B Texas 75010 TX</li>
      <li class="row"><svg width="13" height="13" viewBox="0 0 24 24"><path fill="#5b2c8f" d="M6.6 10.8a15 15 0 0 0 6.6 6.6l2.2-2.2c.3-.3.7-.4 1-.2 1.1.4 2.3.6 3.6.6.6 0 1 .4 1 1V20c0 .6-.4 1-1 1A17 17 0 0 1 3 4c0-.6.4-1 1-1h3.5c.6 0 1 .4 1 1 0 1.3.2 2.5.6 3.6.1.3 0 .7-.2 1z"/></svg>555.014.2290</li>
      <li class="row"><svg width="14" height="11" viewBox="0 0 24 18"><rect x="1" y="1" width="22" height="16" fill="none" stroke="#5b2c8f" stroke-width="2"/><path d="M1 1l11 9 11-9" fill="none" stroke="#5b2c8f" stroke-width="2"/></svg>info@k7electrical.example</li>
    </ul>
    <div class="socials"><i></i><i></i><i></i><i></i></div>
  </div>
</footer>
<div class="bar">© 2018 Company Name&nbsp; All right reserved</div>

</body>
</html>
```